I want ideas sample designs for my book cover

Hello,

We need a book cover designed in flat and 3D Versions. We would like to have jpg and png for final output and include a copy of the PSD for future revisions.

Here are the basic details:

Title: The Harvest of Quiet Builders
Author: Norman Quillfeather

Dimensions of book:

Was looking at the Pavo website for dimensions. I thought you may want to go on there and look at the different sizes. I used the 6x9” perfect bound US trade size for my book. You will see that this has a spine width of 0.225”, Cover size of 12.48 x 9.25” and spine begins at 6.125”

If you need background info on the author just to get an idea what he does, please check:

http://NormanQuillfeather.example

IMPORTANT: Please see attached document for a more detailed info:

Exact Title Of book
Back Cover
Spine Info
Measurements of book and dimension
Examples of book covers
Norman's photo attached

Thanks,
Darlene

Industry/Entity Type

Life Coaching

Font styles to use
Serif

Requirements
Must have
• Jpg, png and PSD files
• title
• author
• exact dimensions
• front and back cover
• flat and 3d versions

```html
<!DOCTYPE html>
<html lang="en">
<head>
<meta charset="utf-8">
<title>The Harvest of Quiet Builders — Cover Concepts</title>
<link rel="stylesheet" href="https://fonts.googleapis.com/css2?family=Arimo:wght@700&family=Oswald:wght@700&family=PT+Sans+Narrow:wght@400;700&family=Source+Sans+3:wght@400&display=swap">
<style>
  :root {
    --backdrop: #c4c4c4;
    --title-orange: #f26f21;
    --type-white: #ffffff;
    --type-ink: #141414;
    --shade-deep: #10151f;
    --shade-navy: #1d2636;
    --sky-pale: #d3dde5;
    --sky-warm: #f2b878;
    --sea-blue: #2f5f98;
    --sea-deep: #1c3c6e;
  }
  * { margin: 0; padding: 0; box-sizing: border-box; }
  html, body {
    width: 1200px; height: 1200px; overflow: hidden;
    background: var(--backdrop);
  }
  .concepts {
    position: relative; width: 1200px; height: 1200px;
  }
  .cover {
    position: absolute; top: 225px;
    width: 500px; height: 750px;
    box-shadow: 0 8px 24px rgba(0,0,0,0.25);
  }
  .cover--vertical { left: 60px; }
  .cover--stacked { left: 640px; }
  .cover svg { display: block; width: 500px; height: 750px; }

  .title-block { font-family: "Arimo", Arial, sans-serif; font-weight: 700; fill: var(--title-orange); }
  .title-condensed { font-family: "Oswald", Impact, sans-serif; font-weight: 700; fill: var(--title-orange); }
  .title-article { font-family: "Arimo", Arial, sans-serif; font-weight: 700; fill: var(--title-orange); }
  .subtitle { font-family: "Source Sans 3", "Myriad Pro", sans-serif; font-size: 20px; }
  .subtitle--dark { fill: var(--type-ink); }
  .subtitle--light { fill: var(--type-white); }
  .credit-line { font-family: "PT Sans Narrow", sans-serif; font-weight: 400; font-size: 18px; }
  .author-name { font-family: "PT Sans Narrow", sans-serif; font-weight: 700; }
  .on-dark { fill: var(--type-white); }
  .on-light { fill: var(--type-ink); }
</style>
</head>
<body>
<main class="concepts">

  <!-- Concept: vertical title -->
  <section class="cover cover--vertical" aria-label="Cover concept with vertical title">
    <svg viewBox="0 0 500 750" xmlns="http://www.w3.org/2000/svg">
      <defs>
        <linearGradient id="v-photo-x" x1="0" y1="0" x2="1" y2="0">
          <stop offset="0" stop-color="var(--shade-deep)"/>
          <stop offset="0.45" stop-color="var(--shade-navy)"/>
          <stop offset="0.7" stop-color="#9fb0c0"/>
          <stop offset="1" stop-color="var(--sky-pale)"/>
        </linearGradient>
        <linearGradient id="v-photo-y" x1="0" y1="0" x2="0" y2="1">
          <stop offset="0.55" stop-color="var(--sea-blue)" stop-opacity="0"/>
          <stop offset="1" stop-color="var(--sea-deep)" stop-opacity="0.85"/>
        </linearGradient>
      </defs>
      <g role="img" aria-label="Photo: man seen from behind, looking out over the sea">
        <rect width="500" height="750" fill="url(#v-photo-x)"/>
        <rect width="500" height="750" fill="url(#v-photo-y)"/>
      </g>

      <text class="title-block" font-size="88" transform="translate(92,574) rotate(-90)" textLength="540" lengthAdjust="spacingAndGlyphs">HARVEST OF</text>
      <text class="title-block" font-size="88" transform="translate(185,668) rotate(-90)" textLength="630" lengthAdjust="spacingAndGlyphs">QUIET BUILDERS</text>
      <text class="title-article" font-size="42" x="28" y="642">The</text>

      <text class="subtitle subtitle--dark" text-anchor="end">
        <tspan x="466" y="250">How this</tspan>
        <tspan x="466" dy="24">ANCIENT</tspan>
        <tspan x="466" dy="24">WISDOM</tspan>
        <tspan x="466" dy="24">is helping</tspan>
        <tspan x="466" dy="24">billionaires,</tspan>
        <tspan x="466" dy="24">INDUSTRY</tspan>
        <tspan x="466" dy="24">ICONS and</tspan>
        <tspan x="466" dy="24">entrepreneurs</tspan>
        <tspan x="466" dy="24">to be better</tspan>
        <tspan x="466" dy="24">LEADERS,</tspan>
        <tspan x="466" dy="24">increase impact</tspan>
        <tspan x="466" dy="24">and leave a LEGACY</tspan>
      </text>

      <text class="credit-line on-dark" x="210" y="625">From the Best Selling Author of “Stillwater”</text>
      <text class="author-name on-dark" font-size="40" x="210" y="672" textLength="270" lengthAdjust="spacingAndGlyphs">Norman Quillfeather</text>
    </svg>
  </section>

  <!-- Concept: stacked title -->
  <section class="cover cover--stacked" aria-label="Cover concept with stacked title">
    <svg viewBox="0 0 500 750" xmlns="http://www.w3.org/2000/svg">
      <defs>
        <linearGradient id="s-sky" x1="0" y1="0" x2="1" y2="0.6">
          <stop offset="0" stop-color="var(--sky-pale)"/>
          <stop offset="1" stop-color="var(--sky-warm)"/>
        </linearGradient>
        <linearGradient id="s-sea" x1="0" y1="0" x2="0" y2="1">
          <stop offset="0" stop-color="#6d8fb4"/>
          <stop offset="0.5" stop-color="var(--sea-blue)"/>
          <stop offset="1" stop-color="var(--sea-deep)"/>
        </linearGradient>
        <linearGradient id="s-figure" x1="0" y1="0" x2="1" y2="0">
          <stop offset="0" stop-color="var(--shade-deep)"/>
          <stop offset="0.8" stop-color="var(--shade-navy)"/>
          <stop offset="1" stop-color="var(--shade-navy)" stop-opacity="0"/>
        </linearGradient>
      </defs>
      <g role="img" aria-label="Photo: man in profile from behind, facing a sunset sea with waves">
        <rect width="500" height="750" fill="url(#s-sky)"/>
        <rect y="360" width="500" height="390" fill="url(#s-sea)"/>
        <rect width="290" height="750" fill="url(#s-figure)"/>
      </g>

      <text class="credit-line on-light" text-anchor="end" x="462" y="250">From the Best Selling Author of “Stillwater”</text>
      <text class="author-name on-light" font-size="46" text-anchor="end" x="464" y="298" textLength="320" lengthAdjust="spacingAndGlyphs">Norman Quillfeather</text>

      <text class="title-article" font-size="30" transform="translate(60,380) rotate(-90)">The</text>
      <text class="title-condensed" font-size="86" x="68" y="392" textLength="396" lengthAdjust="spacingAndGlyphs">HARVEST OF</text>
      <text class="title-condensed" font-size="86" x="30" y="472" textLength="436" lengthAdjust="spacingAndGlyphs">QUIET BUILDERS</text>

      <text class="subtitle subtitle--light">
        <tspan x="38" y="520">How this ancient wisdom is</tspan>
        <tspan x="38" dy="26">helping billionaires, industry</tspan>
        <tspan x="38" dy="26">icons and entrepreneurs to</tspan>
        <tspan x="38" dy="26">be better leaders, increase</tspan>
        <tspan x="38" dy="26">impact and leave a legacy</tspan>
      </text>
    </svg>
  </section>

</main>
</body>
</html>
```